Ridgeline Journeys business card

please see website
www.ridgelinejourneys.comau

info needed on card
Curtis Halvey
Ph
email
Adventure Riding GPS trails

please use my logo and colours off my site

Curtis Halvey
curtis@ridgelinejourneys.com

```html
<!DOCTYPE html>
<html lang="en">
<head>
<meta charset="utf-8">
<title>Ridgeline Journeys – Business Card</title>
<link rel="stylesheet" href="https://fonts.googleapis.com/css2?family=Source+Sans+3:ital,wght@0,400;0,600;0,700;1,700&display=swap">
<style>
  :root {
    --backdrop: #4a4a4a;
    --card-white: #f6f6f6;
    --panel-grey: #5a5a5a;
    --edge-black: #0d0d0d;
    --accent-yellow: #f6d21c;
    --ink-dark: #151515;
    --ink-mid: #444444;
  }
  * { margin: 0; padding: 0; box-sizing: border-box; }
  html, body {
    width: 1200px;
    height: 750px;
    overflow: hidden;
    background: var(--backdrop);
    font-family: "Source Sans 3", "Helvetica Neue", Arial, sans-serif;
  }
  .business-card {
    position: absolute;
    left: 50px;
    top: 61px;
    width: 1100px;
    height: 628px;
    background: var(--card-white);
    overflow: hidden;
  }
  .card-edge-panel {
    position: absolute;
    inset: 0;
    width: 100%;
    height: 100%;
  }
  .brand {
    position: absolute;
    right: 63px;
    top: 110px;
    display: flex;
    align-items: center;
    gap: 22px;
  }
  .brand-dot {
    width: 58px;
    height: 58px;
    border-radius: 50%;
    background: var(--accent-yellow);
  }
  .brand-name {
    font-weight: 700;
    font-size: 46px;
    line-height: 1.0;
    text-transform: uppercase;
    color: var(--ink-dark);
    letter-spacing: 0.5px;
  }
  .contact {
    position: absolute;
    right: 63px;
    top: 303px;
    text-align: right;
  }
  .contact-name {
    font-weight: 600;
    font-size: 38px;
    color: var(--ink-dark);
    line-height: 1;
    margin-bottom: 40px;
  }
  .contact-line {
    font-size: 25px;
    color: var(--ink-mid);
    line-height: 44px;
  }
  .tagline {
    margin-top: 14px;
    font-weight: 700;
    font-style: italic;
    font-size: 29px;
    color: var(--ink-dark);
  }
</style>
</head>
<body>
  <div class="business-card">
    <svg class="card-edge-panel" viewBox="0 0 576 329" preserveAspectRatio="none" aria-hidden="true">
      <polygon points="0,0 138,0 300,329 0,329" fill="var(--panel-grey)"/>
      <polygon points="138,0 150,0 318,329 300,329" fill="var(--edge-black)"/>
    </svg>

    <div class="brand">
      <div class="brand-dot"></div>
      <div class="brand-name">Ridgeline<br>Journeys</div>
    </div>

    <div class="contact">
      <div class="contact-name">Curtis Halvey</div>
      <div class="contact-line">Ph : 612 845 3907</div>
      <div class="contact-line">curtis@ridgelinejourneys.com</div>
      <div class="contact-line">www.ridgelinejourneys.com.au</div>
      <div class="tagline">Adventure Riding GPS trails</div>
    </div>
  </div>
</body>
</html>
```